Luxury Wine Label for New Startup Winery

We need a wine label for our new winery startup. We have worked with a local designer but do not feel the resulting label / logo have the elevation required to present our brand as a luxury wine. Our winery is called "Quailbrook Vineyards" and we are focused on extremely high quality hand crafted artisan and estate wines from the Pacific Northwest.
We would like to see designs that utilize a tree line, or other imagery that represents the "Quailbrook" part of our company name. Another interesting feature could be wood grain.
A logo will be required based on your design so please design with this in mind:
This logo should be consistent with the wine bottle label design, and should be representative of our high end exclusive wine while giving a sense of place (Oregon/ Pacific Northwest.)
I will supply an image of the design we received from our local designer, PLEASE NOTE: in general we do like wood grain and tree line concepts but feel the execution was poorly done.
ATTN: Logo design should be suitable for use on: Bottles (Red wine/rose/white wine), Bussiness cards, vehicle signage, business signage, etc
P.S.:
If you have a design that is not outside the box we are still interested in seeing it.
Label is for a burgundy style bottle with a label height of 3.5 - 4" and a width of 3.5-4"
any label <= 4"x4" and >=3.5"x3.5" will be acceptable:
HOWEVER Width should be greater than or equal to height due to the bottle format
Target Market(s)
Wine enthusiasts with adequate discretionary budgets to afford $100 bottles of wine.
Industry/Entity Type
Wine / Winery
Requirements
Must have
- A sense of luxury, a feel of exclusivity, and a theme consistent with our product and brand name
Nice to have
- Tree line, wood grain or other wood themes. Serif fonts
Should not have
- anything cheesy, off topic, hard to read script fonts or anything that makes the label hard to read from a few feet away or too busy

```html
<!DOCTYPE html>
<html lang="en">
<head>
<meta charset="utf-8">
<title>Quailbrook Vineyards – Syrah Label</title>
<link href="https://fonts.googleapis.com/css2?family=Sorts+Mill+Goudy&family=Libre+Caslon+Text:wght@700&display=swap" rel="stylesheet">
<style>
  :root {
    --page: #ffffff;
    --label-black: #020202;
    --frame-silver: #b9b9b9;
    --gold: #c9a040;
    --gold-light: #f1dc93;
    --gold-deep: #a77b1f;
    --wood-dark: #5e3620;
    --wood-mid: #8a5a38;
    --wood-light: #9c6b47;
  }
  * { margin: 0; padding: 0; box-sizing: border-box; }
  html, body {
    width: 1200px;
    height: 848px;
    overflow: hidden;
    background: var(--page);
  }
  .canvas {
    position: relative;
    width: 1200px;
    height: 848px;
  }
  .label-set {
    position: absolute;
    left: 320px;
    top: 126px;
    width: 560px;
  }

  /* Main black label */
  .front-label {
    position: relative;
    width: 560px;
    height: 454px;
    background: var(--label-black);
  }
  .front-frame {
    position: absolute;
    left: 35px;
    top: 34px;
    right: 34px;
    bottom: 34px;
    border: 1.5px solid var(--frame-silver);
  }
  .treeline {
    position: absolute;
    left: 0;
    top: 0;
    width: 491px;
    height: 186px;
  }
  .brand-name {
    position: absolute;
    left: 0;
    right: 0;
    top: 196px;
    text-align: center;
    font-family: "Sorts Mill Goudy", Georgia, serif;
    color: var(--gold);
    line-height: 0.78;
  }
  .brand-name .brand-line-1 { display: block; font-size: 52px; }
  .brand-name .brand-line-2 { display: block; font-size: 46px; }
  .region {
    position: absolute;
    left: 0;
    right: 0;
    top: 312px;
    text-align: center;
    font-family: "Libre Caslon Text", "Times New Roman", serif;
    font-weight: 700;
    font-size: 34px;
    letter-spacing: 0.5px;
    color: var(--gold);
  }

  /* Wood varietal strip */
  .varietal-label {
    position: relative;
    width: 560px;
    height: 122px;
    margin-top: 18px;
    background: linear-gradient(90deg, var(--wood-mid) 0%, var(--wood-dark) 18%, var(--wood-light) 38%, var(--wood-mid) 55%, var(--wood-dark) 75%, var(--wood-mid) 100%);
  }
  .varietal-frame {
    position: absolute;
    left: 18px;
    right: 18px;
    top: 18px;
    bottom: 18px;
    border: 1.5px solid var(--gold);
    border-bottom: none;
  }
  .varietal-name {
    position: absolute;
    left: 0;
    right: 0;
    top: 15px;
    text-align: center;
    font-family: "Sorts Mill Goudy", Georgia, serif;
    font-size: 66px;
    line-height: 1;
    color: var(--gold-light);
  }
  .vintage-line {
    position: absolute;
    left: 18px;
    right: 18px;
    top: 96px;
    display: flex;
    align-items: center;
    gap: 6px;
  }
  .vintage-rule {
    flex: 1;
    height: 1.5px;
    background: var(--gold);
  }
  .vintage-text {
    font-family: "Libre Caslon Text", "Times New Roman", serif;
    font-weight: 700;
    font-size: 12.5px;
    letter-spacing: 0.6px;
    color: var(--gold);
    white-space: nowrap;
  }
</style>
</head>
<body>
<main class="canvas">
  <section class="label-set">
    <div class="front-label">
      <div class="front-frame">
        <svg class="treeline" role="img" aria-label="Gold foil silhouette of an evergreen tree line with two birds in flight" viewBox="0 0 491 186" xmlns="http://www.w3.org/2000/svg">
          <defs>
            <linearGradient id="gold-foil" x1="0" y1="0" x2="1" y2="0">
              <stop offset="0" stop-color="#a77b1f"/>
              <stop offset="0.25" stop-color="#c9a040"/>
              <stop offset="0.42" stop-color="#f1dc93"/>
              <stop offset="0.6" stop-color="#c79a36"/>
              <stop offset="1" stop-color="#a77b1f"/>
            </linearGradient>
            <linearGradient id="canopy-fade" x1="0" y1="0" x2="0" y2="1">
              <stop offset="0" stop-color="#020202" stop-opacity="1"/>
              <stop offset="0.55" stop-color="#020202" stop-opacity="0"/>
            </linearGradient>
          </defs>
          <polygon points="2,186 2,90 489,70 489,148" fill="url(#gold-foil)"/>
          <polygon points="2,90 489,70 489,148 2,186" fill="url(#canopy-fade)" opacity="0"/>
          <polygon points="2,90 489,70 489,0 2,0" fill="url(#gold-foil)" opacity="0.35"/>
          <rect x="0" y="0" width="491" height="100" fill="url(#canopy-fade)"/>
        </svg>
        <h1 class="brand-name">
          <span class="brand-line-1">Quailbrook</span>
          <span class="brand-line-2">Vineyards</span>
        </h1>
        <p class="region">WILLAMETTE VALLEY</p>
      </div>
    </div>

    <div class="varietal-label" role="img" aria-label="Walnut wood grain strip">
      <div class="varietal-frame"></div>
      <h2 class="varietal-name">Syrah</h2>
      <div class="vintage-line">
        <span class="vintage-rule"></span>
        <span class="vintage-text">ESTATE | 2023 | GROWN</span>
        <span class="vintage-rule"></span>
      </div>
    </div>
  </section>
</main>
</body>
</html>
```